Business Card Design

I already have a company logo for my company. I have a logo for the manufacturer we represent. I want a professional business card design.

```html
<!DOCTYPE html>
<html lang="en">
<head>
<meta charset="utf-8">
<title>Beacon Alert Systems – Business Card</title>
<link rel="stylesheet" href="https://fonts.googleapis.com/css2?family=Montserrat:wght@400;500;700;800&display=swap">
<style>
  :root {
    --backdrop: #b4b4b4;
    --card: #1c1c1e;
    --accent: #e3242b;
    --text-light: #e6e6e6;
    --text-muted: #bdbdbd;
  }
  * { margin: 0; padding: 0; box-sizing: border-box; }
  html, body {
    width: 1200px;
    height: 900px;
    overflow: hidden;
    background: var(--backdrop);
    font-family: "Montserrat", sans-serif;
  }
  .sheet {
    position: relative;
    width: 1200px;
    height: 900px;
  }
  .card {
    position: absolute;
    left: 250px;
    width: 700px;
    height: 400px;
    background: var(--card);
    border-bottom: 3px solid var(--accent);
    box-shadow: 0 6px 18px rgba(0,0,0,0.25);
  }
  .card--front { top: 35px; }
  .card--back { top: 465px; }

  .brand {
    display: flex;
    align-items: center;
    gap: 14px;
  }
  .brand__mark {
    width: 22px;
    height: 22px;
    background: var(--accent);
    flex: none;
  }
  .brand__name {
    color: var(--text-light);
    font-weight: 800;
    font-size: 26px;
    line-height: 1.15;
    letter-spacing: 1px;
    text-transform: uppercase;
  }

  .card--front .brand {
    position: absolute;
    left: 55px;
    top: 160px;
  }
  .divider {
    position: absolute;
    left: 360px;
    top: 95px;
    width: 2px;
    height: 210px;
    background: var(--accent);
  }
  .contact {
    position: absolute;
    left: 395px;
    top: 95px;
    color: var(--text-light);
  }
  .contact__name {
    color: var(--accent);
    font-weight: 700;
    font-size: 24px;
  }
  .contact__role {
    font-size: 14px;
    color: var(--text-muted);
    margin-top: 2px;
  }
  .contact__address {
    font-size: 14px;
    margin-top: 18px;
    line-height: 1.35;
  }
  .contact__lines {
    list-style: none;
    margin-top: 16px;
    font-size: 14px;
  }
  .contact__lines li {
    display: flex;
    align-items: center;
    gap: 10px;
    line-height: 1.6;
  }
  .contact__lines svg {
    width: 12px;
    height: 12px;
    flex: none;
  }

  .card--back .brand {
    position: absolute;
    left: 50%;
    top: 50%;
    transform: translate(-50%, -50%);
  }
  .card--back .brand__name { font-size: 34px; }
  .card--back .brand__mark { width: 28px; height: 28px; }
</style>
</head>
<body>
<main class="sheet">
  <section class="card card--front">
    <div class="brand">
      <span class="brand__mark"></span>
      <span class="brand__name">Beacon Alert<br>Systems</span>
    </div>
    <div class="divider"></div>
    <div class="contact">
      <p class="contact__name">Daniel Carver</p>
      <p class="contact__role">Managing Director</p>
      <p class="contact__address">2840 Alder Row<br>Millbrook, CO 80455</p>
      <ul class="contact__lines">
        <li>
          <svg viewBox="0 0 12 12" aria-hidden="true"><path d="M2 1h2.5l1 3-1.5 1a6 6 0 0 0 3 3l1-1.5 3 1V10a1 1 0 0 1-1 1A9 9 0 0 1 1 2a1 1 0 0 1 1-1z" fill="var(--accent)"/></svg>
          555.014.0297
        </li>
        <li>
          <svg viewBox="0 0 12 12" aria-hidden="true"><rect x="0.5" y="2" width="11" height="8" fill="var(--accent)"/><path d="M0.5 2l5.5 4.5L11.5 2" stroke="var(--card)" stroke-width="1" fill="none"/></svg>
          info@beaconalertsystems.com
        </li>
        <li>
          <svg viewBox="0 0 12 12" aria-hidden="true"><circle cx="6" cy="6" r="5" fill="none" stroke="var(--accent)" stroke-width="1.4"/><path d="M1 6h10M6 1c-2.5 3-2.5 7 0 10M6 1c2.5 3 2.5 7 0 10" stroke="var(--accent)" stroke-width="1" fill="none"/></svg>
          www.beaconalertsystems.com
        </li>
      </ul>
    </div>
  </section>

  <section class="card card--back">
    <div class="brand">
      <span class="brand__mark"></span>
      <span class="brand__name">Beacon Alert<br>Systems</span>
    </div>
  </section>
</main>
</body>
</html>
```